Orthobiologic, StemCell, Bone Marrow Aspirate Device Distributor

We need a wordpress fully functioning website design for an innovative ortho-biologic, Bone Marrow Aspirate Device that extracts stem cells for orthopedic regenerative medical professionals. We also offer state of the art training in there office setting with licensed medical staff, a full service support team, and software for tracking patient outcome over time. We are an innovative company that prides itself on gold standard support. We will have other offerings on our website and would like a spot for "future" products. We would like to see designs that look professional, medical, and convey support, security, science, and innovation. We prefer shades of blue and red/orange. I particularly like the following websites that also sell the same device in order of preference:regenacelltherapy.comhttps://aspire-medical.eu/marrow-cellution/https://www.matrixbiosurgical.com/#emerging-solutions-in-healthcareElite2elite.comI have attached a few pictures of the device for reference

Target Market(s)

Orthopedics, Regenerative medicine doctors, Industry representatives, Hospitals

Industry/Entity Type

Medical Equipment

Coding

Coded - Design and coding required

Colors
3176b5
33a6d7
f37022
ec1f27

Requirements
Must have
• It must be able to have videos which I can supply, email, online ordering, and sfax. I have a domain name Coralweavesolutions.com . It must have a FAQ section which you can obtain some information from https://www.tolvenclinical.com/solutions#resources
• The device is manufactured by Dulmor and this is the link to the product page http://www.dulmor.com/quintadraw
• I am currently working on a custom logo and should be able to supply that in short order. I prefer shades of blue and red.
Nice to have
• I would love to have a graphic video as seen here: please see quinta draw vs bone marrow aspirate concentrate.
• https://www.tolvenclinical.com/solutions#competition
• I would pay considerably more to have something similar if it is at all possible
Should not have
• Nothing specific

```html
<!DOCTYPE html>
<html lang="en">
<head>
<meta charset="utf-8">
<title>Coral Weave Solutions</title>
<link href="https://fonts.googleapis.com/css2?family=Montserrat:wght@500;600;700&family=Poppins:wght@400;500;600&display=swap" rel="stylesheet">
<style>
:root{
  --blue-deep:#0b3f7a;
  --blue:#3176b5;
  --blue-light:#33a6d7;
  --orange:#f37022;
  --red:#ec1f27;
  --ink:#3a3a3a;
  --text:#6d6d6d;
  --grey-bg:#f1f1f1;
  --footer:#1b1311;
  --white:#ffffff;
}
*{box-sizing:border-box;margin:0;padding:0}
html,body{width:1200px;height:3919px;overflow:hidden}
body{font-family:"Poppins",sans-serif;color:var(--text);background:var(--white)}
.page{position:relative;width:1200px;height:3919px;overflow:hidden}
.abs{position:absolute}
h1,h2,h3{font-family:"Montserrat",sans-serif;font-weight:500;color:var(--ink);letter-spacing:1px}

/* header + hero */
.hero{left:0;top:0;width:1200px;height:692px;overflow:hidden}
.hero-photo{position:absolute;inset:0;background:radial-gradient(circle at 25% 22%,#2f86d6 0,#0d4fa0 18%,transparent 32%),radial-gradient(circle at 78% 12%,#2f8ae0 0,#0b4a96 14%,transparent 26%),radial-gradient(circle at 60% 60%,#1a6fc6 0,transparent 40%),linear-gradient(160deg,#0a2f66 0%,#0d4d9c 45%,#082a5c 100%)}
.hero-cut{position:absolute;left:0;top:0;width:1200px;height:692px}
.brand{left:170px;top:30px;font-family:"Montserrat",sans-serif;font-weight:500;font-size:22px;color:var(--white);letter-spacing:.3px;white-space:nowrap}
.nav{right:175px;top:38px;display:flex;gap:25px;list-style:none}
.nav li{font-family:"Montserrat",sans-serif;font-weight:600;font-size:12px;color:var(--white);letter-spacing:.3px}
.hero-title{left:0;width:1200px;top:288px;text-align:center;font-size:40px;font-weight:600;color:var(--white);letter-spacing:1.5px}
.hero-sub{left:0;width:1200px;top:348px;text-align:center;font-family:"Montserrat",sans-serif;font-weight:600;font-size:15px;color:var(--white);letter-spacing:.5px}
.hero-rule{left:433px;top:389px;width:335px;height:3px;background:linear-gradient(90deg,transparent,var(--white),transparent)}
.dots{left:561px;top:567px;display:flex;gap:7px}
.dots span{width:11px;height:11px;border-radius:50%;background:var(--white)}

/* buttons */
.btn-blue{display:flex;align-items:center;justify-content:center;border-radius:20px;background:linear-gradient(90deg,var(--blue),var(--blue-light));color:var(--white);font-family:"Montserrat",sans-serif;font-weight:500;font-size:14px;letter-spacing:.5px}
.btn-line{display:flex;align-items:center;justify-content:center;border:2px solid var(--orange);border-radius:18px;color:var(--orange);font-family:"Montserrat",sans-serif;font-weight:600;font-size:12px}

/* welcome */
.welcome-title{left:0;width:1200px;top:730px;text-align:center;font-size:46px;line-height:48px}
.center-copy{left:270px;width:660px;text-align:center;font-size:12px;line-height:24px}

/* video */
.video-band{left:0;top:1090px;width:1200px;height:603px;background:var(--grey-bg)}
.video-title{left:170px;top:1222px;font-size:46px}
.video-copy{left:170px;top:1286px;width:310px;font-size:11.5px;line-height:23.4px;color:#555}
.video-frame{left:513px;top:1189px;width:605px;height:408px;background:linear-gradient(135deg,#b9b5ab 0%,#8d8478 40%,#5b6470 75%,#3d5a7a 100%)}

/* products */
.products-title{left:0;width:1200px;top:1765px;text-align:center;font-size:46px}
.card{top:1916px;width:271px;height:408px;border:1px solid #e3e3e3;background:var(--white)}
.card-img{position:absolute;left:39px;top:20px;width:192px;height:192px;border-radius:50%}
.card h3{position:absolute;top:233px;width:100%;text-align:center;font-size:18px;font-weight:600;letter-spacing:.5px}
.card p{position:absolute;top:267px;left:22px;width:227px;text-align:center;font-size:12px;line-height:21px}
.card .btn-line{position:absolute;left:78px;top:346px;width:114px;height:32px}

/* therapy */
.therapy{left:0;top:2411px;width:1200px;height:620px;background:radial-gradient(circle at 75% 40%,#f98b3f 0,#f37022 35%,#ec4a1a 100%)}
.circle-img{border-radius:50%;border:5px solid var(--white)}
.therapy-title{left:586px;top:2522px;font-size:44px;line-height:46px;color:var(--white)}
.therapy-list{left:586px;top:2640px;width:440px;list-style:none;color:var(--white);font-size:12px;line-height:17px}
.therapy-list li{position:relative;padding-left:12px;margin-bottom:18px}
.therapy-list li::before{content:"";position:absolute;left:0;top:6px;width:5px;height:5px;border-radius:50%;background:var(--white)}

/* faq */
.faq-title{left:0;width:1200px;top:3088px;text-align:center;font-size:46px}
.faq-item{left:271px;width:658px;border:2px solid #e9e9e9;border-radius:3px;display:flex;align-items:center;padding-left:48px;font-family:"Montserrat",sans-serif;font-weight:500;font-size:13.5px;line-height:21px;color:#4a4a4a;letter-spacing:.3px}
.faq-item::before{content:"+";position:absolute;left:15px;top:50%;transform:translateY(-50%);width:22px;height:22px;border-radius:50%;background:var(--orange);color:var(--white);font-size:17px;line-height:21px;text-align:center}

/* footer */
.footer{left:0;top:3626px;width:1200px;height:293px;background:var(--footer)}
.foot-head{font-family:"Montserrat",sans-serif;font-weight:600;font-size:18px;color:var(--white);top:3662px}
.foot-links{top:3699px;list-style:none;color:var(--white);font-size:11.5px;line-height:21px}
.email{left:709px;top:3702px;width:234px;height:28px;border-radius:14px 0 0 14px;background:#3a3330;color:#cfcfcf;font-size:11px;padding:7px 12px}
.signup{left:943px;top:3702px;width:84px;height:28px;border-radius:0 14px 14px 0;background:var(--orange);color:var(--white);font-family:"Montserrat",sans-serif;font-weight:600;font-size:12px;display:flex;align-items:center;justify-content:center}
.follow{left:709px;top:3759px;font-family:"Montserrat",sans-serif;font-weight:600;font-size:18px;color:var(--white)}
.social{top:3761px;width:23px;height:23px;border-radius:50%}
.foot-rule{left:172px;top:3856px;width:855px;height:1px;background:#3d3431}
.copyright{left:0;width:1200px;top:3871px;text-align:center;color:var(--white);font-size:11.5px}
</style>
</head>
<body>
<div class="page">

  <section class="abs hero">
    <div class="hero-photo" role="img" aria-label="Microscopic view of blue stem cells"></div>
    <svg class="hero-cut" viewBox="0 0 1200 692" aria-hidden="true">
      <polygon points="0,692 1200,650 1200,605" fill="#33a6d7"/>
      <polygon points="0,692 1200,650 1200,692" fill="#ffffff"/>
    </svg>
  </section>
  <div class="abs brand">Coral Weave Solutions</div>
  <ul class="abs nav">
    <li>HOME</li><li>ABOUT</li><li>PRODUCTS</li><li>PROVIDERS</li><li>RESOURCES</li><li>FAQ</li><li>CONTACT</li>
  </ul>
  <h1 class="abs hero-title">AUTOLOGOUS STEM CELLTHERAPY</h1>
  <p class="abs hero-sub">IMPLEMENTING BONE MARROW DERIVED STEM CELLS IN YOURPRACTICE</p>
  <div class="abs hero-rule"></div>
  <div class="abs dots"><span></span><span></span><span></span><span></span><span></span></div>

  <h2 class="abs welcome-title">WELCOME TO<br>CORAL WEAVE SOLUTIONS</h2>
  <p class="abs center-copy" style="top:862px">Sed ut perspiciatis unde omnis iste natus error sit voluptatem accusantium doloremque laudantium, totam rem aperiam, eaque ipsa quae ab illo inventore veritatis et quasi architecto beatae vitae dicta licabo Nemo enim ipsam voluptatem quia voluptas sit aspernatur aut odit aut fugit, sed quia consequuntur magni dolores eos qui ratione voluptatem sequi nesciunque porro quisquam esti dolorem.</p>
  <div class="abs btn-blue" style="left:529px;top:978px;width:140px;height:37px">READ MORE</div>

  <section class="abs video-band"></section>
  <h2 class="abs video-title">OUR VIDEO</h2>
  <p class="abs video-copy">Sed ut perspiciatis unde omnis iste natus error sit voluptatem accusantium doloremque lauda ntium, totam rem aperiam, eaque ipsa quae ab illo inventore veritatis et quasi architecto beate vitae dicta licaboemo enim ipsam voluptateuia voluptas sit aspernatur aut odit aut fugit, sedlou ia consequuntur magni dolores eos qui ratione voluptatem sequi nesciunque porro quisquam esti dolorem.</p>
  <div class="abs btn-blue" style="left:170px;top:1515px;width:140px;height:36px">READ MORE</div>
  <div class="abs video-frame" role="img" aria-label="Video still of a gloved clinician performing a knee injection"></div>
  <svg class="abs" style="left:768px;top:1346px" width="94" height="94" viewBox="0 0 94 94" aria-label="Play video">
    <circle cx="47" cy="47" r="44" fill="none" stroke="#ffffff" stroke-width="3"/>
    <polygon points="38,30 38,64 64,47" fill="none" stroke="#ffffff" stroke-width="3" stroke-linejoin="round"/>
  </svg>

  <h2 class="abs products-title">FUTURE PRODUCTS</h2>
  <p class="abs center-copy" style="top:1831px">Sed ut perspiciatis unde omnis iste natus error sit voluptatem accusantium doloremque laudantium, totam rem aperiam, eaque ipsa quae ab illo inventore veritatis et quasi architecto beatae</p>

  <article class="abs card" style="left:172px">
    <div class="card-img" role="img" aria-label="Aspiration device in its tray" style="background:linear-gradient(180deg,#6b1414 0%,#8c2a2a 40%,#d9d9dc 60%,#b8bcc4 100%)"></div>
    <h3>Loersptisun</h3>
    <p>Sed ut perspiciatis unde omnis iste natus error sit voluptatem accusium doloremque laudantiuotam</p>
    <div class="btn-line">Read More</div>
  </article>
  <article class="abs card" style="left:464px">
    <div class="card-img" role="img" aria-label="Illustration of a cell being injected" style="background:radial-gradient(circle at 45% 55%,#f29a3a 0,#d9441f 22%,#1b4d9a 45%,#0a2a5e 100%)"></div>
    <h3>Loersptisun</h3>
    <p>Sed ut perspiciatis unde omnis iste natus error sit voluptatem accusium doloremque laudantiuotam</p>
    <div class="btn-line">Read More</div>
  </article>
  <article class="abs card" style="left:756px">
    <div class="card-img" role="img" aria-label="Laboratory pipetting into a sample plate" style="background:linear-gradient(160deg,#eef3f8 0%,#b9d4ea 40%,#3f8fd8 60%,#5b5f6e 100%)"></div>
    <h3>Loersptisun</h3>
    <p>Sed ut perspiciatis unde omnis iste natus error sit voluptatem accusium doloremque laudantiuotam</p>
    <div class="btn-line">Read More</div>
  </article>

  <section class="abs therapy"></section>
  <div class="abs circle-img" role="img" aria-label="Illustration of pink stem cells" style="left:158px;top:2543px;width:390px;height:390px;background:radial-gradient(circle at 60% 45%,#e64f8a 0,#b8406f 25%,#7c8bc9 55%,#b6c2e6 100%)"></div>
  <div class="abs circle-img" role="img" aria-label="Illustration of a needle entering bone marrow" style="left:53px;top:2540px;width:274px;height:274px;background:radial-gradient(circle at 50% 50%,#c4476a 0,#d86583 50%,#e28aa0 100%)"></div>
  <h2 class="abs therapy-title">AUTOLOGOUS<br>STEM CELLTHERAPY</h2>
  <ul class="abs therapy-list">
    <li>Cell based therapy is giving your body the opportunity to heal itself, you healing you.</li>
    <li>Marrow Stem Cells are our body’s natural repair mechanism when we sustain injuries to include wear and tear on our joints.</li>
    <li>Our body stores stem cells in our bone marrow, and calls them into action when an injury occurs. This process is called vasculogenisis.</li>
    <li>As we age our marrow still has stored stem cells, but in fewer numbers and we lose the ability to mobilize these cells as effectively to heal our injuries.</li>
    <li>Mechanically aspirating and transplanting marrow cells to a defect area exactly mimics and supplements your body’s natural response to injury.</li>
  </ul>

  <h2 class="abs faq-title">FAQS</h2>
  <div class="abs faq-item" style="top:3162px;height:67px">CAN THE QUINTA DRAW NEEDLE BE USED TO ASPIRATE FROM<br>BONES OTHER THAN THE ILIAC CREST?</div>
  <div class="abs faq-item" style="top:3240px;height:49px">WHAT IS THE IMPORTANCE OF CD34 COMPARED TO NUCLEATED CELL COUNTS?</div>
  <div class="abs faq-item" style="top:3297px;height:51px">DO THE NUMBER OF CFU-F CELLS IN MARROW DECLINE WITH AGE?</div>
  <div class="abs faq-item" style="top:3360px;height:68px">WHAT IS THE RELATIONSHIP BETWEEN AGE AND ASPIRATION QUALITY<br>FOR BONE MARROW?</div>
  <div class="abs faq-item" style="top:3439px;height:69px">DO CERTAIN MEDICATIONS IMPACT THE NUMBER OF CD34+ CELLS &amp;<br>CFU-F IN THE MARROW?</div>
  <div class="abs faq-item" style="top:3518px;height:50px">WHAT IS THE PURPOSE OF CENTRIFUGATION PROTOCOLS FOR MARROW?</div>

  <footer class="abs footer"></footer>
  <div class="abs foot-head" style="left:172px">Support</div>
  <div class="abs foot-head" style="left:353px">Company</div>
  <div class="abs foot-head" style="left:517px">Links</div>
  <div class="abs foot-head" style="left:709px">Newsletter</div>
  <ul class="abs foot-links" style="left:172px"><li>Sed ut perspiciatis</li><li>Unde omnis iste</li><li>Voluptatem</li><li>Accusantium</li><li>Doloremque</li><li>Laudantium</li></ul>
  <ul class="abs foot-links" style="left:353px"><li>Sed ut perspiciatis</li><li>Unde omnis iste</li><li>Voluptatem</li><li>Accusantium</li><li>Doloremqu</li></ul>
  <ul class="abs foot-links" style="left:517px"><li>Sed ut perspiciatis</li><li>Unde omnis iste</li><li>Voluptatem</li><li>Accusantium</li><li>Doloremque</li><li>Laudantium</li></ul>
  <div class="abs email">Email:</div>
  <div class="abs signup">SIGN UP</div>
  <div class="abs follow">Follow us on</div>
  <div class="abs social" style="left:839px;background:var(--blue)"></div>
  <div class="abs social" style="left:867px;background:var(--blue-light)"></div>
  <div class="abs foot-rule"></div>
  <p class="abs copyright">© 2019 All Rights Are Reserved.Terms of Use | Privacy Policy</p>

</div>
</body>
</html>
```